Dietitian needs awesome business card

I need a contemporary design that's eye catching but professional.
My card is to given to doctors, specialists and patients alike.
I manage patients with chronic diseases
I have uploaded my logo and current business card, I would also like the other Certified Clinical Nutritionist logo incorporated into the design

Target Market(s)

Doctors, specialists and patients

Industry/Entity Type

Healthcare

Contact Information for Business Card

www.brightfieldnutrition.com.au
Ph: 0427 561 903
Fax: 6457 2183
email: marcus.k.diet@fernmail.com
Space on the back of the card with: Appointment date, Appointment time and appointment location

Font styles to use
Serif

Colors
fbee3e
876aae
ffc214

Requirements
Must have
• My Logo
• Certified Clinical Nutritionist Logo
• My 4 locations - Pinebrook Medical Centre, North Corrin Health, Hollis Medical, Ashcombe Doctors Surgery
Nice to have
• I like the colours in my current business card

```html
<!DOCTYPE html>
<html lang="en">
<head>
<meta charset="utf-8">
<title>Brightfield Nutrition &amp; Dietetics – Business Card</title>
<link rel="stylesheet" href="https://fonts.googleapis.com/css2?family=Ubuntu:wght@400&family=Open+Sans:wght@400&display=swap">
<style>
  :root{
    --bg:#d9d9d9;
    --card:#ffffff;
    --navy:#26378f;
    --navy-deep:#17287d;
    --navy-light:#3f63b8;
    --green:#8cc63f;
    --text:#555a60;
    --rule:#a9abae;
    --orange:#f47b20;
    --faint:#eef1f8;
  }
  *{box-sizing:border-box;margin:0;padding:0}
  html,body{width:1105px;height:1200px;overflow:hidden}
  body{background:var(--bg);position:relative;font-family:"Open Sans",Arial,sans-serif;color:var(--text)}
  .card{position:absolute;left:182px;width:746px;height:425px;background:var(--card);overflow:hidden}
  .card--front{top:120px}
  .card--back{top:637px}

  /* front */
  .brand-band{position:absolute;left:0;top:61px;width:87px;height:102px;
    background:linear-gradient(90deg,var(--navy-deep),var(--navy-light))}
  .brand-mark{position:absolute;left:53px;top:57px;width:96px;height:96px;border-radius:50%;background:var(--green)}
  .brand-name{position:absolute;left:157px;top:82px;font-family:"Ubuntu",Arial,sans-serif;font-weight:400;color:var(--navy);line-height:1}
  .brand-name__main{display:block;font-size:44px}
  .brand-name__sub{display:block;font-size:19px;margin-top:4px}
  .decor-circle{position:absolute;left:380px;top:-60px;width:520px;height:520px;border-radius:50%;
    background:radial-gradient(circle at 45% 40%,#f1f4fa 0%,#f3f8ec 60%,rgba(255,255,255,0) 72%)}
  .person{position:absolute;left:156px;top:185px;font-family:"Ubuntu",Arial,sans-serif}
  .person__name{font-size:27px;color:var(--navy);line-height:1.2}
  .person__role{font-size:19px;color:var(--green);margin-top:4px}
  .contact{position:absolute;left:160px;top:258px;list-style:none}
  .contact li{display:flex;align-items:center;height:29px;font-size:19px;color:var(--text)}
  .contact svg{width:18px;height:18px;margin-right:9px;fill:var(--navy)}

  /* back */
  .back-mark{position:absolute;left:48px;top:40px;display:flex;align-items:center}
  .back-mark__dot{width:60px;height:60px;border-radius:50%;background:var(--green);margin-right:12px}
  .back-mark__name{font-family:"Ubuntu",Arial,sans-serif;font-size:22px;color:var(--navy)}
  .credential{position:absolute;left:518px;top:39px;width:178px;height:84px;background:var(--orange);border-radius:3px;
    display:flex;align-items:center;justify-content:space-between;padding:0 12px 0 10px}
  .credential__text{color:#fff;font-size:13px;line-height:1.3;width:100px}
  .credential__seal{width:52px;height:52px;border-radius:50%;background:#fff}
  .note-line{position:absolute;left:50px;width:643px;height:0;border-top:1px solid var(--rule)}
  .appt{position:absolute;left:50px;top:278px;width:643px;display:flex;align-items:baseline;color:var(--navy)}
  .appt__label{font-size:21px;margin-right:8px}
  .appt__fill{border-bottom:2px dotted var(--navy);height:14px;margin-right:14px}
  .appt__fill--date{width:290px}
  .appt__fill--time{width:142px;margin-right:4px}
  .appt__unit{font-size:15px}
  .locations{position:absolute;left:50px;top:330px;width:660px;display:grid;grid-template-columns:375px 1fr;row-gap:8px;list-style:none}
  .locations li{display:flex;align-items:center;font-size:20px;color:var(--text)}
  .locations li::before{content:"";width:17px;height:17px;border:1.5px solid var(--navy);margin-right:8px}
</style>
</head>
<body>

<section class="card card--front" aria-label="Business card front">
  <div class="decor-circle"></div>
  <div class="brand-band"></div>
  <div class="brand-mark"></div>
  <div class="brand-name">
    <span class="brand-name__main">Brightfield</span>
    <span class="brand-name__sub">Nutrition &amp; Dietetics</span>
  </div>
  <div class="person">
    <p class="person__name">Marcus Kellaway</p>
    <p class="person__role">Nutritionist &amp; Chef</p>
  </div>
  <ul class="contact">
    <li><svg viewBox="0 0 24 24" aria-hidden="true"><path d="M6.6 10.8a15.1 15.1 0 0 0 6.6 6.6l2.2-2.2c.3-.3.7-.4 1-.2 1.1.4 2.3.6 3.6.6.6 0 1 .4 1 1V20c0 .6-.4 1-1 1A17 17 0 0 1 3 4c0-.6.4-1 1-1h3.5c.6 0 1 .4 1 1 0 1.2.2 2.4.6 3.6.1.3 0 .7-.2 1z"/></svg>0427 561 903</li>
    <li><svg viewBox="0 0 24 24" aria-hidden="true"><path d="M6 2h10v5H6zM3 8h18a1 1 0 0 1 1 1v8h-4v5H4v-5H2V9a1 1 0 0 1 1-1zm4 9v3h10v-3z"/></svg>6457 2183</li>
    <li><svg viewBox="0 0 24 24" aria-hidden="true"><path d="M2 5h20v14H2zm2 2v.5l8 5 8-5V7z"/></svg>marcus.k.diet@fernmail.com</li>
    <li><svg viewBox="0 0 24 24" aria-hidden="true"><circle cx="12" cy="12" r="10"/><path d="M7 8c2 0 3 1 3 3s-2 1-2 3 2 2 2 4M15 5c0 2 2 2 2 4s-2 2-2 4 2 2 3 2" stroke="#fff" stroke-width="1.6" fill="none"/></svg>brightfieldnutrition.com.au</li>
  </ul>
</section>

<section class="card card--back" aria-label="Business card back">
  <div class="back-mark">
    <span class="back-mark__dot"></span>
    <span class="back-mark__name">Brightfield</span>
  </div>
  <div class="credential">
    <span class="credential__text">Certified Clinical Nutritionist</span>
    <span class="credential__seal"></span>
  </div>
  <div class="note-line" style="top:166px"></div>
  <div class="note-line" style="top:206px"></div>
  <div class="note-line" style="top:247px"></div>
  <div class="appt">
    <span class="appt__label">Date :</span><span class="appt__fill appt__fill--date"></span>
    <span class="appt__label">Time :</span><span class="appt__fill appt__fill--time"></span>
    <span class="appt__unit">AM/PM</span>
  </div>
  <ul class="locations">
    <li>Pinebrook Medical Centre</li>
    <li>Ashcombe Doctors Surgery</li>
    <li>North Corrin Health</li>
    <li>Hollis Medical</li>
  </ul>
</section>

</body>
</html>
```